Brightfen Business Card Redesign & Logo Update

We need to update our business cards to something more modern and fresh. Brightfen can provide the current color schemes and old design examples, but welcome creativity in helping us with this redesign. PLEASE NOTE that we no longer utilize the "tree" and/or "leaf" imagery in our branding. If able would apprecaite an update on the quality of our "words only" logo in Ai. / PNG formats too.

Target Market(s)

Investors, landowners, corporate partners, contractors

Industry/Entity Type

Environmental Restoration & Conservation

Contact Information for Business Card

Logo, persons name, title, mailing address, phone and email, website url

Font styles to use
Other font styles liked:
• Merriweather

Requirements
Nice to have
• Logo, persons name, title, mailing address, phone and email, website url, but open to ideams
Should not have
• No all back backgrounds

```html
<!DOCTYPE html>
<html lang="en">
<head>
<meta charset="utf-8">
<title>Brightfen Business Card</title>
<link rel="stylesheet" href="https://fonts.googleapis.com/css2?family=Merriweather:wght@400;700;900&display=swap">
<style>
  :root {
    --bg: #e6e8ea;
    --paper: #ffffff;
    --green: #15803f;
    --green-dark: #0f6a33;
    --leaf-light: #8cc63f;
    --ink: #1f2a33;
    --white: #ffffff;
  }
  * { box-sizing: border-box; margin: 0; padding: 0; }
  html, body { width: 1200px; height: 780px; overflow: hidden; }
  body {
    background: var(--bg);
    font-family: "Merriweather", Georgia, serif;
    display: flex;
    align-items: center;
    justify-content: center;
    gap: 40px;
  }
  .card {
    position: relative;
    width: 540px;
    height: 310px;
    background: var(--paper);
    border-radius: 18px;
    overflow: hidden;
    box-shadow: 0 6px 18px rgba(0,0,0,0.12);
  }

  /* Front */
  .front__foliage {
    position: absolute;
    left: 0; top: 0;
    width: 230px; height: 190px;
    background: radial-gradient(ellipse at 20% 30%, var(--leaf-light) 0%, var(--green) 60%, rgba(21,128,63,0) 100%);
    border-bottom-right-radius: 100% 90%;
    opacity: 0.9;
  }
  .front__brand {
    position: absolute;
    left: 200px; top: 120px;
    font-weight: 900;
    font-size: 52px;
    color: var(--green);
    letter-spacing: -0.5px;
  }
  .front__web {
    position: absolute;
    left: 204px; top: 200px;
    font-size: 15px;
    color: var(--green);
  }

  /* Back */
  .back__frame {
    position: absolute;
    inset: 10px;
    border: 1.5px solid var(--green);
    border-radius: 4px;
  }
  .back__brand {
    position: absolute;
    left: 34px; top: 56px;
    font-weight: 900;
    font-size: 40px;
    color: var(--green);
  }
  .back__person {
    position: absolute;
    right: 34px; top: 46px;
    text-align: center;
    color: var(--ink);
  }
  .back__name { font-weight: 700; font-size: 21px; letter-spacing: 1.5px; }
  .back__title { font-size: 8px; letter-spacing: 4px; margin-top: 5px; }
  .back__panel {
    position: absolute;
    left: 160px; right: 0; bottom: 0;
    height: 165px;
    background: var(--green);
    color: var(--white);
    padding: 20px 0 0 34px;
    display: flex;
    flex-direction: column;
    gap: 10px;
  }
  .contact { display: flex; align-items: center; gap: 14px; }
  .contact__icon {
    width: 32px; height: 32px;
    border-radius: 50%;
    background: var(--white);
    display: flex; align-items: center; justify-content: center;
    flex: none;
  }
  .contact__text { font-size: 11.5px; line-height: 1.45; }
</style>
</head>
<body>

  <section class="card card--front">
    <div class="front__foliage" role="img" aria-label="Area for a green foliage illustration"></div>
    <div class="front__brand">Brightfen</div>
    <div class="front__web">www.brightfen.com</div>
  </section>

  <section class="card card--back">
    <div class="back__frame"></div>
    <div class="back__brand">Brightfen</div>
    <div class="back__person">
      <div class="back__name">DANIEL HARROW</div>
      <div class="back__title">FOUNDER</div>
    </div>
    <div class="back__panel">
      <div class="contact">
        <span class="contact__icon">
          <svg width="16" height="16" viewBox="0 0 24 24"><path fill="#15803f" d="M6.6 10.8a15 15 0 0 0 6.6 6.6l2.2-2.2a1 1 0 0 1 1-.25 11.4 11.4 0 0 0 3.6.57 1 1 0 0 1 1 1V20a1 1 0 0 1-1 1A17 17 0 0 1 3 4a1 1 0 0 1 1-1h3.5a1 1 0 0 1 1 1c0 1.25.2 2.45.57 3.6a1 1 0 0 1-.25 1z"/></svg>
        </span>
        <span class="contact__text">+000 55512 3456<br>+000 55512 3456</span>
      </div>
      <div class="contact">
        <span class="contact__icon">
          <svg width="16" height="16" viewBox="0 0 24 24" fill="none" stroke="#15803f" stroke-width="2"><circle cx="12" cy="12" r="9"/><path d="M3 12h18M12 3c3 3 3 15 0 18M12 3c-3 3-3 15 0 18"/></svg>
        </span>
        <span class="contact__text">www.brightfenrestore.com<br>hello@brightfen.com</span>
      </div>
      <div class="contact">
        <span class="contact__icon">
          <svg width="16" height="16" viewBox="0 0 24 24"><path fill="#15803f" d="M12 2a7 7 0 0 0-7 7c0 5 7 13 7 13s7-8 7-13a7 7 0 0 0-7-7zm0 9.5A2.5 2.5 0 1 1 12 6.5a2.5 2.5 0 0 1 0 5z"/></svg>
        </span>
        <span class="contact__text">48, Marsh Lane Road,<br>Fenland Shire</span>
      </div>
    </div>
  </section>

</body>
</html>
```